Pet sitting Business needs a website

We need a website that shows our services and prices. Shows our love of animals but also our professionalism. want a gallery, about, blog, services, links to fb and instagram accounts, newsletter archive. want it to be easy to access and wonderful to navigate. want the domain to be Birchfordpawhaven.com
take any info from FB site www.facebook.com/birchfordpawhaven
I would like it to fit square space platform

Target Market(s)

upscale area, responsible pet owners,

Industry/Entity Type

Pet Care

Coding

Coded - Design and coding required

Number of Pages Required

5+ page

Font styles to use
Sans Serif

Requirements
Must have
• (square space platform)
• Menu
• photo gallery
• about us
• services
• policies
• monthly newsletter
• unavailable dates
• Introduction (welcome)
• payment methods
• Daily updates
• testimonials (use from fb site)
Should not have
• stock photos

```html
<!DOCTYPE html>
<html lang="en">
<head>
<meta charset="utf-8">
<title>Birchford Paw Haven</title>
<link href="https://fonts.googleapis.com/css2?family=Roboto:ital,wght@0,300;0,400;0,500;0,700;1,300;1,400&family=Covered+By+Your+Grace&display=swap" rel="stylesheet">
<style>
:root{
  --nav-blue:#1f7fb5;
  --footer-blue:#1b78ae;
  --sky:#3fb0ea;
  --deep:#1a82c0;
  --gold:#e0a21d;
  --ink:#222;
  --muted:#666;
  --white:#fff;
  --grey:#bdbdbd;
}
*{box-sizing:border-box;margin:0;padding:0}
html,body{width:1200px;height:2195px;overflow:hidden}
body{position:relative;font-family:'Roboto',sans-serif;background:var(--white);color:var(--ink)}
.abs{position:absolute}

/* top bar */
.topbar{left:0;top:0;width:1200px;height:35px;background:var(--white)}
.topbar .info{top:9px;font-size:14px;color:#888;display:flex;align-items:center;gap:5px}
.reserve{left:944px;top:7px;width:132px;height:21px;background:var(--gold);color:var(--white);font-size:13px;font-weight:700;border-radius:3px;text-align:center;line-height:21px}
.social-dot{width:11px;height:11px;border-radius:50%;background:#999;top:12px}

/* nav */
.navband{left:0;top:35px;width:1200px;height:70px;background:var(--nav-blue)}
.logo{left:54px;top:0;width:286px;height:114px;background:var(--white);border-radius:0 0 10px 10px;display:flex;align-items:center;justify-content:center;gap:10px}
.logo .mark{width:30px;height:30px;border-radius:50%;background:var(--gold)}
.logo .name{font-size:24px;font-weight:500;color:var(--gold)}
.menu a{position:absolute;top:62px;transform:translateX(-50%);color:var(--white);font-size:16px;font-weight:500;text-decoration:none;white-space:nowrap}

/* hero */
.hero{left:0;top:105px;width:1200px;height:483px;background:radial-gradient(ellipse at 70% 40%,#b08a4c 0%,#8c6a36 45%,#5e4622 100%)}
.hero-title{left:40px;top:222px;width:485px;text-align:center;font-family:'Covered By Your Grace',cursive;font-size:58px;line-height:54px;color:var(--white)}
.btn-light{height:33px;background:var(--white);color:var(--nav-blue);font-size:11px;font-weight:700;text-align:center;line-height:33px;border-radius:2px}
.dots{left:570px;top:559px;display:flex;gap:8px}
.dots span{width:10px;height:10px;border-radius:50%;background:var(--white)}
.dots span.off{background:transparent;border:1.5px solid var(--white)}

/* intro */
.intro{left:0;top:588px;width:1200px;height:275px;background:linear-gradient(100deg,#2f8fcd 0%,#4aaee0 60%,#2b86c3 100%)}
.intro h1{position:absolute;left:53px;top:28px;font-size:28px;font-weight:500;color:var(--white)}
.intro p{position:absolute;left:53px;width:716px;font-size:13px;line-height:19px;color:var(--white)}
.portrait{left:815px;top:640px;width:250px;height:250px;transform:rotate(-3deg);border:8px solid var(--gold);background:linear-gradient(135deg,#5a4a3a,#2a241e 60%,#3f7a34);box-shadow:0 3px 10px rgba(0,0,0,.35);z-index:2}

/* parallax */
.parallax{left:0;top:863px;width:1200px;height:271px;background:linear-gradient(180deg,#8a8276 0%,#7a5236 45%,#5a3a26 100%)}
.parallax-caption{left:20px;top:1106px;font-size:17px;font-weight:700;color:var(--white);letter-spacing:.3px}

/* services */
.services{left:0;top:1134px;width:1200px;height:332px;background:radial-gradient(ellipse at 50% 100%,#46b8f0 0%,#2898d6 45%,#1d84c2 100%)}
.section-title{position:absolute;left:0;width:1200px;text-align:center;font-size:22px;font-weight:500}
.services .section-title{top:38px;color:var(--white)}
.rule-dotted{left:53px;top:1213px;width:1096px;border-top:2px dotted rgba(255,255,255,.8)}
.service{top:1250px;width:200px;transform:translateX(-50%);text-align:center;color:var(--white)}
.service svg{height:74px;display:block;margin:0 auto}
.service h3{margin-top:22px;font-size:19px;font-weight:500}
.col-divider{top:1266px;height:88px;border-left:1.5px dashed rgba(255,255,255,.6)}

/* testimonials */
.testimonials .section-title{top:1480px;color:var(--ink)}
.rule-gold{left:53px;top:1522px;width:1096px;border-top:2px dotted var(--gold)}
.quote{font-size:13px;font-style:italic;font-weight:300;line-height:19px;color:#555}
.author{font-size:13px;font-weight:500;color:var(--ink)}
.avatar{width:79px;height:79px;border-radius:50%;background:var(--grey);color:#333;font-size:10px;display:flex;align-items:center;justify-content:center}
.like-line{left:66px;top:1727px;width:1068px;border-top:1px solid #e3e3e3}
.like-pill{left:376px;top:1702px;width:448px;height:49px;border:1px solid #e3e3e3;border-radius:25px;background:var(--white)}
.like-thumb{left:376px;top:1702px;width:57px;height:49px;border-right:1px solid #e3e3e3;display:flex;align-items:center;justify-content:center}
.like-btn{left:498px;top:1719px;height:17px;padding:0 5px;background:#4267b2;color:var(--white);font-size:10px;font-weight:700;line-height:17px;border-radius:2px}
.like-text{left:548px;top:1720px;font-size:10px;color:#333}

/* footer */
.footer{left:0;top:1763px;width:1200px;height:432px;background:var(--footer-blue)}
.footer h4{position:absolute;top:1813px;font-size:18px;font-weight:500;color:var(--white)}
.footer-text{font-size:13px;line-height:20px;color:var(--white)}
.footer-text b{font-weight:700}
.field{left:334px;width:251px;background:var(--white);border-radius:3px;font-size:13px;color:#999;padding:8px 12px}
.send{left:334px;top:2028px;width:134px;height:32px;background:var(--white);border-radius:3px;font-size:13px;font-weight:500;color:var(--ink);text-align:center;line-height:32px}
.map{left:615px;top:1854px;width:253px;height:209px;background:linear-gradient(135deg,#e7e2d6 0%,#d8e6c8 40%,#a9cce8 100%)}
.quote-mark{left:901px;top:1850px;font-size:64px;font-weight:700;color:rgba(255,255,255,.4);font-style:italic;line-height:64px}
.footer-rule{left:53px;top:2132px;width:1096px;border-top:1px solid rgba(255,255,255,.35)}
.copyright{left:0;top:2158px;width:1200px;text-align:center;font-size:13px;font-weight:500;color:var(--white)}
.footer-social{top:2037px;width:13px;height:13px;border-radius:50%;background:var(--white)}
</style>
</head>
<body>

<header>
  <div class="abs topbar">
    <div class="abs info" style="left:557px">
      <svg width="12" height="12" viewBox="0 0 24 24"><path fill="#888" d="M6.6 10.8a15 15 0 0 0 6.6 6.6l2.2-2.2a1 1 0 0 1 1-.25 11.4 11.4 0 0 0 3.6.57 1 1 0 0 1 1 1V20a1 1 0 0 1-1 1A17 17 0 0 1 3 4a1 1 0 0 1 1-1h3.5a1 1 0 0 1 1 1c0 1.25.2 2.45.57 3.57a1 1 0 0 1-.25 1z"/></svg>
      512-306-7140
    </div>
    <div class="abs info" style="left:689px">
      <svg width="13" height="10" viewBox="0 0 26 20"><rect width="26" height="20" rx="2" fill="#888"/><path d="M1 2l12 9 12-9" stroke="#fff" stroke-width="2" fill="none"/></svg>
      birchfordpawhaven@gmail.com
    </div>
    <div class="abs reserve">Online Reservations</div>
    <div class="abs social-dot" style="left:1101px"></div>
    <div class="abs social-dot" style="left:1137px"></div>
  </div>

  <div class="abs navband"></div>
  <div class="abs logo"><span class="mark"></span><span class="name">Birchford Paw Haven</span></div>
  <nav class="menu">
    <a style="left:515px">HI !</a>
    <a style="left:603px">ABOUT US</a>
    <a style="left:715px">SERVICES</a>
    <a style="left:824px">GALLERY</a>
    <a style="left:915px">BLOG</a>
    <a style="left:1007px">POLICIES</a>
    <a style="left:1114px">CONTACT</a>
  </nav>
</header>

<section>
  <div class="abs hero" role="img" aria-label="Photo of a dog resting its head beside a plush teddy bear"></div>
  <h2 class="abs hero-title">Where Kisses<br>and Hugs are my<br>Speciality</h2>
  <div class="abs btn-light" style="left:145px;top:421px;width:101px">OUR SERVICES</div>
  <div class="abs btn-light" style="left:281px;top:421px;width:105px">GO ON SURFING</div>
  <div class="abs dots"><span class="off"></span><span></span><span></span><span></span></div>
</section>

<section>
  <div class="abs intro">
    <h1>Hi my name is Maren Holloway</h1>
    <p style="top:80px">I would love to introduce myself. I am a Licensed Veterinarian Technician from Nashville, Tennessee. My family and I moved to San Antonio in 2008. I have dedicated the last 13 years to raising my 2 beautiful children and 5 of my furry babies.</p>
    <p style="top:137px">I have the knowledge and the training to give the special care your pet will need. I was a Licensed Veterinarian Technician Supervisor of a major animal hospital in Nashville. I have spent 20 years of my life taking care of our friends and would to do the same for yours.</p>
  </div>
  <div class="abs portrait" role="img" aria-label="Framed photo of the pet sitter with her dog"></div>
</section>

<section>
  <div class="abs parallax" role="img" aria-label="Photo of two curly brown puppies lying on the ground"></div>
  <div class="abs parallax-caption">Parallax image move on mause scroll</div>
</section>

<section>
  <div class="abs services"><h2 class="section-title">Our Services</h2></div>
  <div class="abs rule-dotted"></div>

  <div class="abs service" style="left:148px">
    <svg viewBox="0 0 80 74"><path fill="#fff" d="M40 4a18 18 0 0 0-18 18c0 14 18 40 18 40s18-26 18-40A18 18 0 0 0 40 4zm0 25a7 7 0 1 1 0-14 7 7 0 0 1 0 14z"/><path fill="#fff" opacity=".75" d="M16 20a12 12 0 0 0-12 12c0 9 12 26 12 26s12-17 12-26a12 12 0 0 0-12-12zM64 20a12 12 0 0 0-12 12c0 9 12 26 12 26s12-17 12-26a12 12 0 0 0-12-12z"/></svg>
    <h3>Daily Visit</h3>
  </div>
  <div class="abs service" style="left:369px">
    <svg viewBox="0 0 80 74" role="img" aria-label="Paw prints icon"><g fill="#fff"><circle cx="18" cy="14" r="7"/><circle cx="56" cy="24" r="7"/><circle cx="22" cy="44" r="7"/><circle cx="60" cy="58" r="7"/></g></svg>
    <h3>Just walks</h3>
  </div>
  <div class="abs service" style="left:590px">
    <svg viewBox="0 0 80 74" role="img" aria-label="Potty icon"><g fill="#fff"><ellipse cx="40" cy="62" rx="30" ry="10"/><ellipse cx="40" cy="46" rx="22" ry="9"/><ellipse cx="40" cy="32" rx="14" ry="8"/><circle cx="40" cy="16" r="8"/></g></svg>
    <h3>Potty visits</h3>
  </div>
  <div class="abs service" style="left:809px">
    <svg viewBox="0 0 80 74" role="img" aria-label="Dog park icon"><rect x="16" y="10" width="48" height="58" rx="24" fill="#fff"/></svg>
    <h3>Dog park</h3>
  </div>
  <div class="abs service" style="left:1030px">
    <svg viewBox="0 0 80 74" role="img" aria-label="Medication jar icon"><rect x="24" y="2" width="32" height="10" rx="2" fill="none" stroke="#fff" stroke-width="4"/><rect x="20" y="14" width="40" height="56" rx="6" fill="none" stroke="#fff" stroke-width="4"/><circle cx="40" cy="44" r="10" fill="#fff"/></svg>
    <h3>Medication</h3>
  </div>

  <div class="abs col-divider" style="left:244px"></div>
  <div class="abs col-divider" style="left:465px"></div>
  <div class="abs col-divider" style="left:686px"></div>
  <div class="abs col-divider" style="left:907px"></div>
</section>

<section class="testimonials">
  <h2 class="section-title">What People Say</h2>
  <div class="abs rule-gold"></div>

  <p class="abs quote" style="left:56px;top:1578px;width:406px;text-align:right">Duis aute irure dolor in reprehenderit in voluptate velit esse cillum dolore eu fugiat nulla pariatur. Excepteur sint occaecat cupidatat non proident, sunt in culpa qui officia deserunt mollit.</p>
  <p class="abs author" style="left:56px;top:1648px;width:406px;text-align:right">Owen Pratt, Operations Manager</p>
  <div class="abs avatar" style="left:489px;top:1580px">170x170</div>

  <div class="abs" style="left:600px;top:1580px;height:100px;border-left:1px dashed #ddd"></div>

  <div class="abs avatar" style="left:632px;top:1580px">170x170</div>
  <p class="abs quote" style="left:739px;top:1578px;width:400px">Provident, similique sunt in culpa qui officia deserunt mollitia animi, id est laborum et dolorum fuga. Et harum quidem rerum facilis est et expedita distinctio. Nam libero tempore, cum soluta nobis.</p>
  <p class="abs author" style="left:739px;top:1648px">Clara Whitby, Creative Designer</p>

  <div class="abs like-line"></div>
  <div class="abs like-pill"></div>
  <div class="abs like-thumb"><svg width="16" height="16" viewBox="0 0 24 24"><path d="M2 10h4v11H2zM8 21h9l4-8v-3h-7l1-5-2-2-5 7z" fill="none" stroke="#bbb" stroke-width="1.5"/></svg></div>
  <div class="abs like-btn">✓ Like</div>
  <div class="abs like-text">You and 4.1k others like this.</div>
</section>

<footer>
  <div class="abs footer"></div>

  <h4 style="left:53px">Contact Us</h4>
  <div class="abs footer-text" style="left:53px;top:1854px;width:240px">Maecenas etos sit amet, consectetur adipiscing elit. Terminal volutpat rutrum metro amet sollicitudin interdum.</div>
  <div class="abs footer-text" style="left:53px;top:1927px"><b>Phone:</b> +1 (800) 555 01 42</div>
  <div class="abs footer-text" style="left:53px;top:1961px"><b>Office:</b> 418 Elm Row, New York</div>
  <div class="abs footer-text" style="left:53px;top:1994px"><b>Email:</b> hello@birchfordpawhaven.com</div>
  <div class="abs footer-social" style="left:53px"></div>
  <div class="abs footer-social" style="left:81px"></div>
  <div class="abs footer-social" style="left:109px"></div>
  <div class="abs footer-social" style="left:138px"></div>
  <div class="abs footer-social" style="left:166px"></div>

  <h4 style="left:334px">Feel Free to Mail</h4>
  <div class="abs field" style="top:1856px;height:32px">Name *</div>
  <div class="abs field" style="top:1907px;height:32px">Email *</div>
  <div class="abs field" style="top:1958px;height:50px">Write Your Message Here...</div>
  <div class="abs send">SEND MESSAGE</div>

  <h4 style="left:615px">Find Us</h4>
  <div class="abs map" role="img" aria-label="Street map of the New York area"></div>

  <h4 style="left:901px">Last Review</h4>
  <div class="abs quote-mark">“</div>
  <div class="abs footer-text" style="left:957px;top:1856px;width:200px;line-height:19.5px">Lorem ipsum dolor sit amet, consectetur adipiscing elit, sed do eiusmod tempor incididunt ut labore et dolore magna aliqua. Ut enim ad minim veniam, quis nostrud exercitation ullamco.</div>
  <div class="abs avatar" style="left:901px;top:1980px;width:78px;height:78px;background:#c8c8c8;font-size:13px">84x84</div>
  <div class="abs" style="left:994px;top:1994px;font-size:17px;color:var(--white)">Henry Dalton</div>
  <div class="abs" style="left:994px;top:2026px;font-size:13px;color:var(--white)">Creative Designer</div>

  <div class="abs footer-rule"></div>
  <div class="abs copyright">Copyright 2020. All Rights Reserved</div>
</footer>

</body>
</html>
```